BRELWINCare.co.uk - Mental Health Clinic for Child and Adolescents

Updated 29/01/2018***
I am not sure you guys are getting the idea regards to the opening page / homescreen layout. Can you look at the new images I have uploaded (page 5, 6 and 7) These are some of the layouts I like but to incorporate my chosen images, with the BRELWIN commissioner, buttons and a sliding header bar.
I have written a strong brief, I am looking for a website, preferably wordpress as i know they are easy to maintain. I am looking for a one page site, with the top / opening page being full screen image with drop down categories. I have made a rough design, see full brief in word doc attached, there is some freedom to play around with the design aspect but it will need to relay all the content provided. I like a minimal feel. I have also attached some images that may be useful, but will need a new logo for BRELWIN Care. I have attached some logo idea's, it is up to you decide whether you want to use them.
I would prefer the homepage as full screen image, and the categories offered as a drop down or over the main image.
I have also attached linked to some competitors websites:
https://www.vorimant-health.co.uk/
http://www.qlbn.org.uk/
Industry/Entity Type
Clinic
Number of Pages Required
1 page
Font styles to use
Look and feel
Each slider illustrates characteristics of the customer's brand and the style your logo design should communicate.

```html
<!DOCTYPE html>
<html lang="en">
<head>
<meta charset="utf-8">
<title>BRELWIN Care – Book an Appointment</title>
<link href="https://fonts.googleapis.com/css2?family=Lato:wght@400;700;900&display=swap" rel="stylesheet">
<style>
:root{
  --pink:#e5007d;
  --purple:#7e2676;
  --ink:#1f1f1f;
  --grey-text:#5a5a5a;
  --field:#ececec;
  --white:#ffffff;
}
*{box-sizing:border-box;margin:0;padding:0}
html,body{width:1134px;height:1200px;overflow:hidden;background:var(--white);font-family:'Lato',sans-serif;color:var(--ink)}
.page{position:relative;width:1134px;height:1200px}

.site-header{position:absolute;top:0;left:0;width:1134px;height:106px;background:var(--white)}
.brand{position:absolute;left:112px;top:24px;display:flex;align-items:center;gap:10px}
.brand-dot{width:50px;height:50px;border-radius:50%;background:var(--pink)}
.brand-text{display:flex;flex-direction:column}
.brand-name{font-weight:900;font-size:26px;color:var(--purple);line-height:1}
.brand-sub{font-size:9px;color:var(--grey-text);line-height:1.2;margin-top:4px;width:116px}
.main-nav{position:absolute;left:346px;top:42px;display:flex;gap:18px}
.main-nav a{font-size:13.5px;font-weight:700;color:var(--ink);text-decoration:none;letter-spacing:-.2px}

.hero{position:absolute;top:106px;left:0;width:1134px;height:356px;
  background:linear-gradient(100deg,#8a6a55 0%,#b89a86 30%,#d9d2ca 55%,#c7a58a 80%,#8d7262 100%)}
.hero-title{position:absolute;left:142px;top:145px;font-size:33px;font-weight:700;color:var(--white);letter-spacing:-.3px}

.booking{position:absolute;left:111px;top:530px;width:903px;height:377px;border:1.5px solid var(--pink);border-radius:70px}
.booking-mark{position:absolute;left:50%;top:-22px;transform:translateX(-50%);width:76px;height:44px;background:var(--white);display:flex;justify-content:center;align-items:center}
.booking-mark span{width:36px;height:36px;border-radius:50%;background:#f5e400}
.booking-title{position:absolute;top:52px;width:100%;text-align:center;font-size:27px;font-weight:700;color:var(--grey-text);letter-spacing:-.3px}
.field-label{position:absolute;font-size:14px;color:var(--grey-text)}
.field{position:absolute;background:var(--field);border:none;border-radius:2px}
.submit{position:absolute;left:371px;top:315px;width:162px;height:45px;border:none;border-radius:23px;background:var(--pink);color:var(--white);font-family:'Lato',sans-serif;font-weight:700;font-size:17px}

.call-line{position:absolute;top:940px;left:0;width:1134px;display:flex;justify-content:center;align-items:center;gap:2px}
.call-line .lead{font-size:16px;font-weight:700;color:var(--pink);margin-right:6px}
.call-line .number{font-size:19px;font-weight:700;color:var(--purple)}

.site-footer{position:absolute;top:1014px;left:0;width:1134px;height:186px;background:var(--purple);color:var(--white)}
.footer-nav{position:absolute;top:38px;width:100%;display:flex;justify-content:center;gap:18px}
.footer-nav a{color:var(--white);text-decoration:none;font-size:15.5px;font-weight:700;letter-spacing:-.2px}
.copyright{position:absolute;top:74px;width:100%;text-align:center;font-size:15px}
.social{position:absolute;top:116px;left:481px;display:flex;gap:7px}
.social span{width:41px;height:41px;border:2px solid var(--white);border-radius:50%}
</style>
</head>
<body>
<div class="page">
  <header class="site-header">
    <div class="brand">
      <span class="brand-dot"></span>
      <div class="brand-text">
        <span class="brand-name">BRELWIN</span>
        <span class="brand-sub">Young People's Wellbeing &amp; Support Clinic</span>
      </div>
    </div>
    <nav class="main-nav">
      <a href="#">ABOUT US</a><a href="#">OUR TEAM</a><a href="#">OUR SERVICES</a><a href="#">BLOGS</a><a href="#">FORUM</a><a href="#">CONTACT US</a><a href="#">PARENTS</a><a href="#">COMMISIONERS</a>
    </nav>
  </header>

  <section class="hero" role="img" aria-label="Photo of a young woman working on a laptop in a bright living room">
    <h1 class="hero-title">BOOK AN APPOINTMENT</h1>
  </section>

  <section class="booking">
    <div class="booking-mark"><span></span></div>
    <h2 class="booking-title">BOOK AN APPOINTMENT FORM</h2>
    <label class="field-label" style="left:72px;top:106px">Full Name</label>
    <label class="field-label" style="left:331px;top:106px">Phone</label>
    <label class="field-label" style="left:584px;top:106px">Email address</label>
    <div class="field" style="left:72px;top:131px;width:247px;height:37px"></div>
    <div class="field" style="left:330px;top:131px;width:247px;height:37px"></div>
    <div class="field" style="left:583px;top:131px;width:247px;height:37px"></div>
    <label class="field-label" style="left:70px;top:181px">Your Message</label>
    <div class="field" style="left:72px;top:207px;width:758px;height:85px"></div>
    <button class="submit">SUBMIT NOW</button>
  </section>

  <div class="call-line">
    <svg width="20" height="20" viewBox="0 0 24 24"><path fill="#e5007d" d="M6.6 10.8a15.1 15.1 0 0 0 6.6 6.6l2.2-2.2c.3-.3.7-.4 1-.2 1.1.4 2.3.6 3.6.6.6 0 1 .4 1 1V20c0 .6-.4 1-1 1A17 17 0 0 1 3 4c0-.6.4-1 1-1h3.5c.6 0 1 .4 1 1 0 1.3.2 2.5.6 3.6.1.3 0 .7-.2 1z"/></svg>
    <span class="lead">CALL US NOW AT</span><span class="number">(020) 555 0187</span>
  </div>

  <footer class="site-footer">
    <nav class="footer-nav">
      <a href="#">ABOUT US</a><a href="#">OUR TEAM</a><a href="#">OUR SERVICES</a><a href="#">BLOGS</a><a href="#">CONTACT US</a><a href="#">PARENTS</a><a href="#">COMMISIONERS</a>
    </nav>
    <p class="copyright">© 2018 Company Name&nbsp; All right reserved</p>
    <div class="social"><span></span><span></span><span></span><span></span></div>
  </footer>
</div>
</body>
</html>
```